Dell Corvin - Acoustic Album Cover

I am a musical artist releasing my first full-length solo album. It is composed of nine original "percussive" acoustic fingerstyle songs. Some of my earlier recordings (not for this album) are available at http://www.tunelodge.net/dellcorvin for reference. I am looking for creative album art and need both a front cover and back cover/track listing for physical CD replication and online album art purposes. I am open to a more "natural" design using the pictures included in the uploaded files section or to a more artistic design that doesn't use any of the included pictures at all. The name of the album is "Driftwood", and artist is "Dell Corvin" (me). The track list is:

01) Orchard Shuffle
02) Tumbleweed
03) Glimpses of Perlow
04) Wound Up
05) Walk Along
06) The Quiet Ridge
07) Unfolding
08) Evening on Barrow Lane
09) Lucinda's Tune

Here are some album art examples from professional acoustic artists in the same style as a reference:

https://img.vidplexo.net/v/QwLmZr8NeYt/cover.jpg
http://strumvault.net/wp-content/uploads/2009/12/Low-Meadow-cover-reduced.jpg
https://plinkhouse.examplecdn.net/ImageGen.ashx?image=/media/10608/Teo-Bandry.jpg&width=500
https://files.openfolio.net/commons/1/11/Paul_Vesterby-Tidewater_album.jpg
https://direct.songrivet.net/imageserver/images/Alb.000000000/500x500.jpg
https://pics.shopvarlo.net/images/I/7Kq2mXwPzA1._SY355_.jpg
https://pics.shopvarlo.net/images/I/3Hn9bTyQcL4._SY355_.jpg

As you can see, there is a broad mix of both art-based and photograph-based album covers for artists of this style. I am open to either approach, and an example of each would be preferred if time permits.

Thank you for considering my project and for sharing your artistic talents!

-Dell

Target Market(s)

Music app listeners (Tunora, Melodex, Cadenzo) on any app which displays the album art as part of the artist information pane.

Industry/Entity Type

Music Download

Font styles to use
Serif
Sans Serif
Decorative

Colors

Designer to choose colors to be used in the design.

Requirements
Must have
• The project must have the album name and artist name on the front cover artwork, as well as the track listing on the back cover artwork.
Nice to have
• Some original, creative album artwork would be nice to have, but I would settle on well-done picture-based album designs (photos included) as well.
Should not have
• The project should not have too "stuffy" of a feel (similar to a lot of classical guitar album artwork which usually features the artist in a turtleneck smiling at the camera with guitar in lap).

```html
<!DOCTYPE html>
<html lang="en">
<head>
<meta charset="utf-8">
<title>Dell Corvin – Driftwood album artwork</title>
<link href="https://fonts.googleapis.com/css2?family=Kaushan+Script&family=Montserrat:wght@400;500&display=swap" rel="stylesheet">
<style>
  :root {
    --backdrop: #dcdcdc;
    --ink-light: #ffffff;
    --front-trim: #5d7266;
    --front-door-top: #40536a;
    --front-door-mid: #27384c;
    --front-shirt: #6f8599;
    --front-trousers: #1d2229;
    --front-wood: #c9a06c;
    --front-floor: #1b1c20;
    --back-brick-light: #a4563c;
    --back-brick-dark: #5a2a1c;
    --back-shirt: #4d6a86;
    --back-wood: #d8b894;
    --shadow: rgba(0, 0, 0, 0.28);
  }
  * { margin: 0; padding: 0; box-sizing: border-box; }
  html, body {
    width: 1200px;
    height: 665px;
    overflow: hidden;
    background: var(--backdrop);
  }
  .canvas { position: relative; width: 1200px; height: 665px; }

  .cover {
    position: absolute;
    overflow: hidden;
    box-shadow: 0 6px 14px var(--shadow);
  }
  .cover--front { left: 142px; top: 100px; width: 478px; height: 460px; }
  .cover--back  { left: 636px; top: 74px;  width: 444px; height: 428px; }

  .cover__photo { position: absolute; inset: 0; }
  .cover--front .cover__photo {
    background:
      radial-gradient(ellipse 22% 30% at 78% 78%, var(--front-wood) 0%, rgba(201,160,108,0.55) 55%, rgba(201,160,108,0) 100%),
      radial-gradient(ellipse 34% 24% at 42% 10%, var(--front-shirt) 0%, rgba(111,133,153,0) 100%),
      radial-gradient(ellipse 22% 50% at 38% 62%, var(--front-trousers) 0%, rgba(29,34,41,0) 100%),
      linear-gradient(90deg, var(--front-trim) 0%, var(--front-trim) 11%, rgba(0,0,0,0) 13%, rgba(0,0,0,0) 90%, var(--front-trim) 92%),
      linear-gradient(180deg, var(--front-door-top) 0%, var(--front-door-mid) 75%, var(--front-floor) 100%);
  }
  .cover--back .cover__photo {
    background:
      radial-gradient(ellipse 26% 22% at 64% 78%, var(--back-wood) 0%, rgba(216,184,148,0.5) 55%, rgba(216,184,148,0) 100%),
      radial-gradient(ellipse 30% 48% at 74% 58%, var(--back-shirt) 0%, rgba(77,106,134,0) 100%),
      linear-gradient(135deg, var(--back-brick-light) 0%, var(--back-brick-dark) 100%);
  }

  .cover__frame { position: absolute; border: 2px solid var(--ink-light); }
  .cover--front .cover__frame { left: 12px; top: 12px; right: 10px; bottom: 10px; }
  .cover--back .cover__frame  { left: 10px; top: 10px; right: 10px; bottom: 11px; }

  .cover__title {
    position: absolute;
    font-family: "Kaushan Script", cursive;
    font-weight: 400;
    color: var(--ink-light);
    line-height: 1.2;
    white-space: nowrap;
    transform: rotate(-3deg);
    transform-origin: left center;
    text-shadow: 0 2px 6px rgba(0,0,0,0.25);
  }
  .cover--front .cover__title { left: 52px; top: 88px; font-size: 96px; }
  .cover--back .cover__title  { left: 34px; top: 18px; font-size: 86px; }

  .cover__artist {
    position: absolute;
    font-family: "Montserrat", sans-serif;
    font-weight: 400;
    color: var(--ink-light);
    text-transform: uppercase;
    white-space: nowrap;
    line-height: 1;
  }
  .cover--front .cover__artist { left: 36px; top: 420px; font-size: 17px; letter-spacing: 0.46em; }
  .cover--back .cover__artist  { left: 33px; top: 394px; font-size: 12px; letter-spacing: 0.3em; }

  .tracklist {
    position: absolute;
    left: 36px;
    top: 188px;
    list-style: none;
    font-family: "Montserrat", sans-serif;
    font-weight: 400;
    font-size: 10px;
    color: var(--ink-light);
    text-transform: uppercase;
    letter-spacing: 0.01em;
  }
  .tracklist__item { height: 21.1px; line-height: 21.1px; white-space: nowrap; }
</style>
</head>
<body>
<main class="canvas">

  <section class="cover cover--front" aria-label="Front cover">
    <div class="cover__photo" role="img" aria-label="Photo of the guitarist standing by a blue wooden door, holding an acoustic guitar by the neck, face out of frame"></div>
    <div class="cover__frame"></div>
    <h1 class="cover__title">Driftwood</h1>
    <p class="cover__artist">« Dell Corvin »</p>
  </section>

  <section class="cover cover--back" aria-label="Back cover">
    <div class="cover__photo" role="img" aria-label="Photo of the guitarist leaning on a red brick wall, playing an acoustic guitar"></div>
    <div class="cover__frame"></div>
    <h2 class="cover__title">Driftwood</h2>
    <ol class="tracklist">
      <li class="tracklist__item">01 » Orchard Shuffle</li>
      <li class="tracklist__item">02 » Tumbleweed</li>
      <li class="tracklist__item">03 » Glimpses of Perlow</li>
      <li class="tracklist__item">04 » Wound Up</li>
      <li class="tracklist__item">05 » Walk Along</li>
      <li class="tracklist__item">06 » The Quiet Ridge</li>
      <li class="tracklist__item">07 » Unfolding</li>
      <li class="tracklist__item">08 » Evening on Barrow Lane</li>
      <li class="tracklist__item">09 » Lucinda's Tune</li>
    </ol>
    <p class="cover__artist">« Dell Corvin »</p>
  </section>

</main>
</body>
</html>
```